Modern Label for cleaning products for the brand Vorlix

We need a label design for our line of cleaning products. The label should feature our logo and an image to identify the product's intended use. I've added our logo and an image for use. This only concerns the design of the label on the front of the bottle.

Label dimensions:
Label 1 (500ml bottle with spray): width 58mm x height 115mm
Label 2: (1L bottle): width 73mm x height 140mm
The design must be consistent for both bottles which you find in the pictures.

The bottles to be labeled are white. See the attachment for a photo of the bottles.

The photo must also appear on the label to identify the product's intended use.

Product information:
Brand: Vorlix
Product: Sanitary Cleaner

This text must be placed on the label:
"Cleans, descales & freshens. followed with this text: "Ideal for quick and powerful cleaning. A ready-to-use product for everyday use."

- Mention the seperate USP's: Sanitary, Bathroom, Toilet, Wet areas

Appearance: This is a consumer product, but it must have a professional appearance. We would like to see a design that use the color blue from our logo.

Target Market(s)

Consumers who take care of their homes and want to maintain it the correct (professional) way

Font styles to use
Sans Serif

Colors
0054AA
0677BA
7BADD7
CADEEF
E8F1F8

Requirements
Must have
• USP's + use of image and logo + blend in 1 design
Nice to have
• Keep the color of the logo in the design
Should not have
• Comic sans

```html
<!DOCTYPE html>
<html lang="en">
<head>
<meta charset="utf-8">
<title>Vorlix Sanitary Cleaner – Front Label</title>
<link href="https://fonts.googleapis.com/css2?family=Lexend:wght@400;500;600;700&family=Roboto+Condensed:wght@400;500&display=swap" rel="stylesheet">
<style>
  :root {
    --brand-deep: #0054aa;
    --brand-blue: #0677ba;
    --brand-sky: #7badd7;
    --brand-mist: #cadeef;
    --brand-ice: #e8f1f8;
    --wave-bright: #08b4ee;
    --accent-yellow: #f4ec1c;
    --green-light: #95cb1e;
    --green-deep: #5c9e16;
    --ink: #111111;
    --navy: #14245a;
    --page: #ffffff;
  }
  * { margin: 0; padding: 0; box-sizing: border-box; }
  html, body { width: 1200px; height: 898px; overflow: hidden; background: var(--page); }
  .canvas { position: relative; width: 1200px; height: 898px; }
  .label {
    position: absolute; left: 425px; top: 100px;
    width: 356px; height: 703px;
    border-radius: 10px; overflow: hidden;
    box-shadow: 0 2px 8px rgba(0,0,0,0.18);
  }
  .label svg { display: block; width: 356px; height: 703px; }
  .brand-name { font-family: "Lexend", sans-serif; font-weight: 700; fill: var(--ink); }
  .claim-small { font-family: "Lexend", sans-serif; font-weight: 400; fill: #fff; }
  .claim-strong { font-family: "Lexend", sans-serif; font-weight: 700; font-style: italic; fill: var(--accent-yellow); }
  .product-title { font-family: "Lexend", sans-serif; font-weight: 600; fill: #fff; }
  .product-sub { font-family: "Lexend", sans-serif; font-weight: 500; fill: #fff; }
  .tab-text { font-family: "Lexend", sans-serif; font-weight: 700; font-style: italic; fill: #fff; }
  .usp-label { font-family: "Lexend", sans-serif; font-weight: 400; fill: var(--navy); }
  .badge-arc { font-family: "Lexend", sans-serif; font-weight: 700; fill: #fff; letter-spacing: 0.5px; }
  .badge-text { font-family: "Lexend", sans-serif; fill: #fff; }
  .badge-text.strong { font-weight: 600; }
  .volume { font-family: "Roboto Condensed", sans-serif; fill: var(--navy); }
  .usp-icon { fill: #fff; }
</style>
</head>
<body>
<div class="canvas">
  <div class="label">
    <svg viewBox="0 0 356 703" xmlns="http://www.w3.org/2000/svg">
      <defs>
        <radialGradient id="skyGlow" cx="0.5" cy="0.28" r="0.75">
          <stop offset="0" stop-color="#ffffff"/>
          <stop offset="0.35" stop-color="var(--brand-ice)"/>
          <stop offset="0.6" stop-color="#8fd2f0"/>
          <stop offset="1" stop-color="var(--brand-deep)"/>
        </radialGradient>
        <linearGradient id="waveFill" x1="0" y1="0" x2="1" y2="1">
          <stop offset="0" stop-color="var(--wave-bright)"/>
          <stop offset="0.55" stop-color="var(--brand-blue)"/>
          <stop offset="1" stop-color="var(--brand-deep)"/>
        </linearGradient>
        <linearGradient id="roomFill" x1="0" y1="0" x2="0" y2="1">
          <stop offset="0" stop-color="#e9ecef"/>
          <stop offset="0.5" stop-color="#9a9b9d"/>
          <stop offset="1" stop-color="#b9b7b4"/>
        </linearGradient>
        <linearGradient id="floorFill" x1="0" y1="0" x2="0" y2="1">
          <stop offset="0" stop-color="#e6eef2"/>
          <stop offset="1" stop-color="#c9d3da"/>
        </linearGradient>
        <linearGradient id="badgeFill" x1="0" y1="0" x2="1" y2="1">
          <stop offset="0" stop-color="var(--green-light)"/>
          <stop offset="1" stop-color="var(--green-deep)"/>
        </linearGradient>
        <path id="badgeArc" d="M16,615 A84,84 0 0 1 178,659"/>
      </defs>

      <!-- sky background -->
      <rect class="sky" width="356" height="703" fill="url(#skyGlow)"/>

      <!-- bathroom photo area -->
      <rect class="room-photo" x="90" y="430" width="266" height="273" fill="url(#roomFill)" role="img" aria-label="Photo of a modern grey-tiled bathroom with shower and washbasin"/>

      <!-- main blue wave -->
      <path class="wave" d="M356,168 C320,215 270,225 200,255 C110,292 45,345 22,430 C10,480 3,540 0,610 L0,620 C90,592 180,560 240,502 C300,452 345,390 356,300 Z" fill="url(#waveFill)"/>
      <path class="wave-edge" d="M356,168 C320,215 270,225 200,255 C110,292 45,345 22,430 C10,480 3,540 0,610" fill="none" stroke="var(--brand-deep)" stroke-width="3"/>
      <path class="usp-band" d="M12,470 C90,455 200,462 270,440 C250,475 220,500 190,515 C120,520 60,515 6,530 Z" fill="var(--brand-sky)" opacity="0.45"/>

      <!-- brand -->
      <circle class="brand-dot" cx="179" cy="102" r="52" fill="#ffffff"/>
      <text class="brand-name" x="179" y="199" font-size="40" text-anchor="middle">Vorlix</text>

      <!-- claim -->
      <text class="claim-small" x="263" y="285" font-size="8.5" text-anchor="middle">A READY-TO-USE</text>
      <text class="claim-strong" x="263" y="299" font-size="13" text-anchor="middle">PRODUCT FOR</text>
      <text class="claim-strong" x="263" y="311" font-size="13" text-anchor="middle">EVERYDAY USE.</text>

      <!-- product name -->
      <text class="product-title" x="190" y="397" font-size="49" text-anchor="middle">Sanitary</text>
      <text class="product-sub" x="191" y="425" font-size="31" text-anchor="middle">Cleaner</text>

      <!-- suitable for tab -->
      <path class="tab" d="M22,456 C40,450 80,452 126,449 C122,462 110,468 96,469 C60,470 30,470 18,474 Z" fill="var(--green-light)"/>
      <text class="tab-text" x="74" y="465" font-size="7.5" text-anchor="middle">SUITABLE FOR</text>

      <!-- USP icons -->
      <g class="usp usp-bathroom">
        <path class="usp-icon" d="M49,484 h16 v2 a7,7 0 0 1 -7,7 h-2 a7,7 0 0 1 -7,-7 z M55,478 a3,3 0 0 1 5,0 v5 h-1.5 v-4.5 a1.5,1.5 0 0 0 -2,0 z"/>
        <text class="usp-label" x="57" y="510" font-size="7.5" text-anchor="middle">Bathroom</text>
      </g>
      <g class="usp usp-toilet">
        <path class="usp-icon" d="M101,476 h8 v6 h-8 z M99,483 h12 a6,5 0 0 1 -4,5 v4 h-4 v-4 a6,5 0 0 1 -4,-5 z"/>
        <text class="usp-label" x="105" y="510" font-size="7.5" text-anchor="middle">Toilet</text>
      </g>
      <g class="usp usp-wet">
        <path class="usp-icon" d="M150,478 c-3,5 -6,8 -6,11 a5,5 0 0 0 10,0 c0,-3 -3,-6 -4,-11 z M156,477 c-1.5,3 -3,4.5 -3,6 a3,3 0 0 0 6,0 c0,-1.5 -1.5,-3 -3,-6 z"/>
        <text class="usp-label" x="152" y="510" font-size="7.5" text-anchor="middle">Wet Areas</text>
      </g>
      <g class="usp usp-sanitary">
        <path class="usp-icon" d="M193,481 l4,-2 l3,9 l-4,2 z M201,478 l4,-1 l2,8 l-5,5 l-2,-3 z"/>
        <text class="usp-label" x="200" y="510" font-size="7.5" text-anchor="middle">Sanitary</text>
      </g>

      <!-- green badge -->
      <circle class="badge" cx="95" cy="644" r="98" fill="url(#badgeFill)" stroke="#ffffff" stroke-width="2.5"/>
      <path class="floor-photo" d="M15,647 V615 A77,52 0 0 1 169,615 V647 Z" fill="url(#floorFill)" stroke="#ffffff" stroke-width="1.5" role="img" aria-label="Photo of a shiny clean tiled floor in a bright room"/>
      <text class="badge-arc" font-size="10"><textPath href="#badgeArc" startOffset="6%">CLEANS, DESCALES &amp; FRESHENS</textPath></text>
      <text class="badge-text" x="90" y="663" font-size="8.5" text-anchor="middle">IDEAL FOR</text>
      <text class="badge-text strong" x="90" y="675" font-size="10" text-anchor="middle">QUICK AND POWERFUL</text>
      <text class="badge-text strong" x="90" y="686" font-size="10" text-anchor="middle">CLEANING.</text>

      <!-- volume -->
      <text class="volume" x="225" y="662" font-size="8">Net</text>
      <text class="volume" x="225" y="670" font-size="8">Wt</text>
      <text class="volume" x="240" y="672" font-size="22">500mL(cm<tspan font-size="12" dy="-9">3</tspan><tspan dy="9">)</tspan></text>
      <text class="volume" x="281" y="686" font-size="11" text-anchor="middle">Sanitary Cleaner</text>
    </svg>
  </div>
</div>
</body>
</html>
```